Penfield Draft Works (PDWorks.net)

We need a Wordpress-based site designed for a client who provides writing and editing services for the IT industry. We have a wireframe complete for the homepage, but need all internal pages designed (based on homepage wireframe) and the entire site coded for WP.

Internal pages include: "Our Work" (with samples & testimonials); "Capabilities" (with sections to address "strategy", "coaching", "writing" and "editing"); "About Us"; and a Contact page.

Will provide all copywriting, writing samples, testimonials, and client logos.

We completely realize/acknowledge the subject matter is visually BORING! Anything at all that can be done to make it look visually appealing would be *great*! Stock photography is fine.

Please feel free to ask any questions whatsoever. Thanks for your time!

```html
<!DOCTYPE html>
<html lang="en">
<head>
<meta charset="utf-8">
<title>Penfield Draft Works – Writing &amp; Editing for IT</title>
<link href="https://fonts.googleapis.com/css2?family=Open+Sans:wght@400;600;700;800&display=swap" rel="stylesheet">
<style>
:root{
  --red:#d0102a;
  --red-dark:#8e0a1c;
  --ink:#1d1d1f;
  --text:#333;
  --muted:#8a8a8a;
  --dark-band:#232323;
  --light:#f4f4f4;
  --white:#fff;
}
*{box-sizing:border-box;margin:0;padding:0}
html,body{width:1200px;height:3104px;overflow:hidden}
body{position:relative;font-family:"Open Sans",Arial,sans-serif;color:var(--text);background:var(--white)}
.abs{position:absolute}
a{color:inherit;text-decoration:none}

/* header + hero */
.hero{left:0;top:0;width:1200px;height:680px;background:var(--red)}
.hero-photo{left:352px;top:112px;width:848px;height:568px;background:linear-gradient(120deg,#e9eef2 0%,#b9c4cd 35%,#5d6a78 70%,#2b3440 100%)}
.brand{left:112px;top:36px;color:var(--white);font-size:25px;font-weight:700}
.nav{right:112px;top:30px;display:flex;align-items:center;gap:34px;color:var(--white);font-size:15px;font-weight:700;letter-spacing:.5px}
.nav .active{border-bottom:3px solid var(--white);padding-bottom:6px}
.btn{display:inline-block;border-radius:40px;font-weight:700;font-size:15px;letter-spacing:.5px;text-align:center}
.btn-white{background:var(--white);color:var(--red);padding:14px 26px}
.headline{left:112px;top:272px;width:480px;height:192px;background:#0c0c0c;color:var(--white);padding:40px 32px;font-size:34px;font-weight:800;line-height:1.22;text-transform:uppercase}
.dots{left:124px;top:612px;display:flex;gap:8px}
.dots span{width:14px;height:14px;border-radius:50%;background:var(--white)}

/* section titles */
.section-title{left:0;width:1200px;text-align:center;font-size:40px;font-weight:800;color:var(--ink)}
.section-title::after{content:"";display:block;width:90px;height:4px;background:var(--red);margin:16px auto 0}
.btn-outline{border:3px solid var(--red);color:var(--ink);background:var(--white);padding:14px 30px;font-size:15px}

/* capabilities */
.cap-card{top:880px;width:232px;height:292px;color:var(--white);overflow:hidden}
.cap-card .fill{position:absolute;inset:0}
.cap-card .label{position:absolute;left:0;right:0;bottom:38px;text-align:center;font-size:20px;font-weight:800;letter-spacing:.5px}
.cap-card .knob{position:absolute;left:50%;bottom:-20px;width:44px;height:44px;margin-left:-22px;border-radius:50%;background:var(--white)}
.cap-card.is-open{background:var(--red);padding:44px 24px;text-align:center}
.cap-card.is-open .label{position:static;margin-bottom:18px}
.cap-card.is-open p{font-size:13px;line-height:1.5}
.cap-card.is-open svg{margin-top:18px}

/* featured */
.featured{left:0;top:1360px;width:1200px;height:360px;background:var(--dark-band)}
.featured .section-title{color:var(--white);top:80px}
.partner{top:172px;width:188px;height:96px;background:var(--white);display:flex;align-items:center;justify-content:center;gap:10px;font-size:19px;font-weight:700;color:var(--ink)}
.partner i{width:20px;height:20px;background:var(--red);border-radius:50%;display:block}

/* work */
.work-card{top:1928px;width:308px;height:384px;background:var(--light)}
.work-card .thumb{height:180px}
.work-card h3{font-size:17px;font-weight:700;color:var(--ink);line-height:1.35;margin:22px 20px 12px}
.work-card p{font-size:13px;color:var(--muted);line-height:1.5;margin:0 20px 12px}
.work-card .more{margin:0 20px;font-size:13px;color:var(--red);border-bottom:1px solid var(--red)}
.play{position:absolute;left:50%;top:90px;width:44px;height:44px;margin:-22px 0 0 -22px;border-radius:50%;background:var(--red)}

/* contact band */
.cta-left{left:0;top:2500px;width:1200px;height:260px;background:linear-gradient(90deg,#2a0a0e,#6e0c18)}
.cta-right{left:0;top:2500px;width:1200px;height:260px}
.cta-text{color:var(--white);font-size:25px;font-weight:700;line-height:1.35}
.btn-red{background:var(--red);color:var(--white);padding:14px 28px}
.email-field{left:668px;top:2660px;width:360px;height:50px;border-radius:30px;background:var(--white);padding:15px 26px;font-size:14px;color:#555}

/* footer */
.footer-title{left:0;top:2800px;width:1200px;text-align:center;font-size:28px;font-weight:700;color:var(--ink)}
.contact-item{top:2880px;display:flex;gap:20px;align-items:flex-start}
.contact-item .ring{width:80px;height:80px;border-radius:50%;border:3px solid #555;display:flex;align-items:center;justify-content:center;flex:none}
.contact-item h4{font-size:19px;font-weight:700;color:var(--ink);margin:6px 0 8px}
.contact-item p{font-size:14px;color:#666;line-height:1.5}
.bottom-bar{left:0;top:3016px;width:1200px;height:88px;border-top:1px solid #ddd;display:flex;align-items:center;justify-content:space-between;padding:0 112px;font-size:13px;color:#666}
.social{display:flex;gap:10px}
.social span{width:26px;height:26px;border-radius:50%;background:#3b5b99;display:block}
.social span:nth-child(2){background:#2aa3e0}
.social span:nth-child(3){background:var(--red)}
</style>
</head>
<body>

<section class="hero abs"></section>
<div class="hero-photo abs" role="img" aria-label="Photo of a businessman typing on a laptop by a bright window"></div>
<div class="brand abs">Penfield Draft Works</div>
<nav class="nav abs">
  <a class="active">HOME</a><a>OUR WORK</a><a>CAPABILITIES</a><a>ABOUT US</a><a>BLOG</a>
  <a class="btn btn-white">GET IN TOUCH</a>
</nav>
<h1 class="headline abs">Communicate your expertise and your customer successes</h1>
<div class="dots abs"><span></span><span></span><span></span></div>

<h2 class="section-title abs" style="top:760px">OUR CAPABILITIES</h2>
<div class="cap-card abs" style="left:112px">
  <div class="fill" role="img" aria-label="Photo of colleagues planning around a desk" style="background:linear-gradient(160deg,#c9b9a6,#6f5a4a)"></div>
  <div class="label">STRATEGY</div><div class="knob"></div>
</div>
<div class="cap-card abs is-open" style="left:360px">
  <div class="label">COACHING</div>
  <p>We help your experts shape clear messages, plan their content and speak with confidence to buyers, partners and the press at every stage.</p>
  <svg width="16" height="10" viewBox="0 0 16 10"><path d="M0 0h16L8 10z" fill="#fff"/></svg>
</div>
<div class="cap-card abs" style="left:608px">
  <div class="fill" role="img" aria-label="Photo of hands writing in a notebook" style="background:linear-gradient(160deg,#d8d2c8,#6b6158)"></div>
  <div class="label">WRITING</div><div class="knob"></div>
</div>
<div class="cap-card abs" style="left:856px">
  <div class="fill" role="img" aria-label="Photo of a person editing on a laptop" style="background:linear-gradient(160deg,#cfc7bf,#5a5049)"></div>
  <div class="label">EDITING</div><div class="knob"></div>
</div>
<a class="btn btn-outline abs" style="left:489px;top:1206px">VIEW OUR CAPABILITIES</a>

<section class="featured abs">
  <h2 class="section-title abs">AS FEATURED IN</h2>
  <div class="partner abs" style="left:112px"><i></i>Brightwell</div>
  <div class="partner abs" style="left:316px"><i></i>Halden</div>
  <div class="partner abs" style="left:520px"><i></i>Marrow Co</div>
  <div class="partner abs" style="left:724px">Ostrel</div>
  <div class="partner abs" style="left:928px;font-size:17px">Carvane Freight</div>
</section>

<h2 class="section-title abs" style="top:1808px">OUR WORK</h2>
<article class="work-card abs" style="left:112px">
  <div class="thumb" role="img" aria-label="Photo of a woman working on a laptop in a cafe" style="background:linear-gradient(150deg,#b7c48a,#5f6b3c)"></div>
  <h3>Nemo enim ipsam voluptatem quia voluptas</h3>
  <p>Short notes on the project, the client goal and the results our writers delivered.</p>
  <a class="more">Read more →</a>
</article>
<article class="work-card abs" style="left:446px;background:var(--white);border:1px solid #e3e3e3">
  <div class="thumb" role="img" aria-label="Video still of a woman at a desk" style="background:linear-gradient(150deg,#e9e9e9,#9c9c9c);position:relative"><span class="play"></span></div>
  <h3>Nemo enim ipsam voluptatem quia voluptas</h3>
  <p>Short notes on the project, the client goal and the results our writers delivered.</p>
  <a class="more">Read more →</a>
</article>
<article class="work-card abs" style="left:780px">
  <div class="thumb" role="img" aria-label="Photo of a woman typing on a laptop at home" style="background:linear-gradient(150deg,#e4d8cc,#8d7a6a)"></div>
  <h3>Nemo enim ipsam voluptatem quia voluptas</h3>
  <p>Short notes on the project, the client goal and the results our writers delivered.</p>
  <a class="more">Read more →</a>
</article>
<a class="btn btn-outline abs" style="left:516px;top:2344px">VIEW OUR WORK</a>

<div class="cta-left abs" role="img" aria-label="Dark red tinted photo of an office workspace"></div>
<svg class="cta-right abs" width="1200" height="260" viewBox="0 0 1200 260"><path d="M660 0H1200V260H590Z" fill="#d0102a"/></svg>
<p class="cta-text abs" style="left:112px;top:2532px;width:420px">Feel free to contact us with any questions.<br>We're happy to help</p>
<a class="btn btn-red abs" style="left:112px;top:2662px;font-size:13px">GET IN TOUCH</a>
<p class="cta-text abs" style="left:668px;top:2532px;width:440px">Editorial inspiration delivered straight to your inbox</p>
<div class="email-field abs">Email address</div>

<h2 class="footer-title abs">Penfield Draft Works</h2>
<div class="contact-item abs" style="left:112px">
  <div class="ring"><svg width="26" height="34" viewBox="0 0 26 34"><path d="M13 1C6 1 1 6 1 13c0 9 12 20 12 20s12-11 12-20C25 6 20 1 13 1z" fill="none" stroke="#444" stroke-width="3"/><circle cx="13" cy="13" r="4" fill="#444"/></svg></div>
  <div><h4>Address:</h4><p>12 Harbor Lane, Suite 4,<br>Portland</p></div>
</div>
<div class="contact-item abs" style="left:460px">
  <div class="ring"><svg width="30" height="30" viewBox="0 0 30 30"><path d="M6 2l6 6-3 4c2 4 5 7 9 9l4-3 6 6-4 4C14 28 2 16 2 6z" fill="#444"/></svg></div>
  <div><h4>Phone:</h4><p>+1 555 014 2290</p></div>
</div>
<div class="contact-item abs" style="left:800px">
  <div class="ring"><svg width="30" height="22" viewBox="0 0 30 22"><rect x="1" y="1" width="28" height="20" rx="2" fill="#444"/><path d="M2 2l13 10L28 2" fill="none" stroke="#fff" stroke-width="2"/></svg></div>
  <div><h4>Email Address:</h4><p>hello@pdworks.net</p></div>
</div>
<footer class="bottom-bar abs">
  <span>© Copyright @2022 Penfield Draft Works | All Rights Reserved</span>
  <div class="social"><span></span><span></span><span></span></div>
</footer>

</body>
</html>
```